Business Card Design

We are a commercial real estate brokerage in San Francisco, leasing office buildings downtown.
I would like a clean, elegant look. Simple but powerful .

Industry/Entity Type

Business

Contact Information for Business Card

Derek Holloway
lic# 07258143
415.555.0172
derek@velt-commercial.example
velt-commercial.example

```html
<!DOCTYPE html>
<html lang="en">
<head>
<meta charset="utf-8">
<title>Velt Commercial — Business Card</title>
<link rel="stylesheet" href="https://fonts.googleapis.com/css2?family=Open+Sans:wght@400;600;700&display=swap">
<style>
  :root {
    --backdrop: #3b302c;
    --card: #f1f1f1;
    --slate-blue: #5f7694;
    --ink: #2f3236;
    --ink-soft: #55595e;
    --divider: #8c9096;
  }
  * { margin: 0; padding: 0; box-sizing: border-box; }
  html, body {
    width: 1200px; height: 768px; overflow: hidden;
    background: var(--backdrop);
    font-family: "Open Sans", Arial, sans-serif;
  }
  .stage {
    position: relative; width: 1200px; height: 768px;
    display: flex; align-items: center; justify-content: center; gap: 50px;
  }
  .card {
    position: relative; width: 525px; height: 300px;
    background: var(--card);
    box-shadow: 0 10px 24px rgba(0,0,0,.45);
  }
  .brand {
    display: flex; align-items: center; gap: 14px;
    color: var(--slate-blue);
  }
  .brand-square {
    width: 34px; height: 34px; background: var(--slate-blue);
  }
  .brand-name {
    font-weight: 700; text-transform: uppercase;
    line-height: 1; letter-spacing: .5px;
  }
  .card-front .brand { position: absolute; left: 118px; top: 112px; }
  .card-front .brand-name { font-size: 38px; }
  .card-front .brand-square { width: 44px; height: 44px; }

  .card-back .side-band {
    position: absolute; left: 14px; top: 0; bottom: 0; width: 36px;
    background: var(--slate-blue);
  }
  .card-back .brand { position: absolute; left: 84px; top: 40px; }
  .card-back .brand-name { font-size: 28px; }
  .holder { position: absolute; left: 84px; top: 118px; }
  .holder-name { font-size: 19px; font-weight: 700; color: var(--ink); }
  .holder-title { font-size: 11.5px; color: var(--ink-soft); margin-top: 2px; }
  .contact {
    position: absolute; left: 84px; top: 184px;
    list-style: none; font-size: 13px; color: var(--ink);
  }
  .contact li { display: flex; align-items: center; gap: 9px; height: 21px; }
  .contact svg { width: 12px; height: 12px; fill: var(--ink-soft); flex: none; }
  .license {
    position: absolute; right: 30px; bottom: 24px;
    font-size: 13px; color: var(--ink);
  }
</style>
</head>
<body>
<main class="stage">
  <section class="card card-front" aria-label="Card front">
    <div class="brand">
      <span class="brand-square"></span>
      <span class="brand-name">Velt Commercial</span>
    </div>
  </section>

  <section class="card card-back" aria-label="Card back">
    <div class="side-band"></div>
    <div class="brand">
      <span class="brand-square"></span>
      <span class="brand-name">Velt Commercial</span>
    </div>
    <div class="holder">
      <p class="holder-name">Derek Holloway</p>
      <p class="holder-title">Managing Director</p>
    </div>
    <ul class="contact">
      <li>
        <svg viewBox="0 0 24 24" aria-hidden="true"><path d="M6.6 10.8a15 15 0 0 0 6.6 6.6l2.2-2.2a1 1 0 0 1 1-.25 11.4 11.4 0 0 0 3.6.57 1 1 0 0 1 1 1V20a1 1 0 0 1-1 1A17 17 0 0 1 3 4a1 1 0 0 1 1-1h3.5a1 1 0 0 1 1 1c0 1.25.2 2.45.57 3.57a1 1 0 0 1-.25 1z"/></svg>
        415.555.0172
      </li>
      <li>
        <svg viewBox="0 0 24 24" aria-hidden="true"><path d="M2 5h20v14H2z M3.5 6.5 12 13l8.5-6.5" fill="none" stroke="#55595e" stroke-width="2"/></svg>
        derek@velt-commercial.example
      </li>
      <li>
        <svg viewBox="0 0 24 24" aria-hidden="true"><circle cx="12" cy="12" r="9.5" fill="none" stroke="#55595e" stroke-width="2"/><path d="M2.5 12h19M12 2.5c3 3 3 16 0 19M12 2.5c-3 3-3 16 0 19" fill="none" stroke="#55595e" stroke-width="1.6"/></svg>
        www.velt-commercial.example
      </li>
    </ul>
    <p class="license">LIC# 07258143</p>
  </section>
</main>
</body>
</html>
```